Varnel Corporate Website for technological company

We need a modern website to promote our product and services.
You can found the actually website at the address: www.varnel-example.ch

We are a new company for B2B market. We would like do show our high precision and innovation capability.

we need a section were is possible to easily upload "news" and documents for our customers.

Target Market(s)

B2B services in the industry market

Industry/Entity Type

It Company

Coding

Coded - Design and coding required

Number of Pages Required

5+ page

Font styles to use
Other font styles liked:
• We accept propositions

Requirements
Must have
• Easy to maintain
• Presentation of the Varnel company
• Presentation of Varnel services and products
• The customer can download our ducumentation
Nice to have
• Sexy and modern

```html
<!DOCTYPE html>
<html lang="en">
<head>
<meta charset="utf-8">
<title>Varnel Ltd. – Systems engineering</title>
<link href="https://fonts.googleapis.com/css2?family=Fira+Sans:wght@300;400;500;600;700&display=swap" rel="stylesheet">
<style>
:root{
  --olive:#b5a874;
  --olive-dark:#5e5634;
  --news-bg:#a99e68;
  --gold-text:#b0a26a;
  --ink:#222;
  --line:#999;
  --white:#fff;
  --photo-light:#e9e9e9;
  --photo-mid:#a8a8a8;
  --photo-dark:#4a4a4a;
}
*{margin:0;padding:0;box-sizing:border-box}
html,body{width:1200px;height:2731px;overflow:hidden}
body{position:relative;background:var(--white);font-family:"Fira Sans",Arial,sans-serif;color:var(--ink)}

/* header */
.site-header{position:absolute;left:0;top:0;width:1200px;height:78px;background:#fff;border-bottom:1px solid #eee}
.brand{position:absolute;display:flex;align-items:center;gap:8px;font-weight:700;font-size:22px;color:#2a2a2a;letter-spacing:.5px}
.brand-mark{width:16px;height:16px;background:var(--olive)}
.site-header .brand{left:200px;top:24px}
.nav-link{position:absolute;top:30px;transform:translateX(-50%);font-size:12px;text-transform:uppercase;color:#333;white-space:nowrap}
.nav-link.active::after{content:"";position:absolute;left:-8px;right:-8px;top:30px;height:3px;background:var(--olive)}
.lang-flag{position:absolute;left:914px;top:31px;width:18px;height:12px;background:linear-gradient(#2a3b8f 0 50%,#c8202f 50% 100%)}
.login-btn{position:absolute;left:956px;top:22px;width:86px;height:31px;background:#8a8a8a;color:#eee;font-size:11px;display:flex;align-items:center;justify-content:center;gap:6px}
.login-btn .dot{width:6px;height:8px;background:var(--olive)}

/* hero */
.hero{position:absolute;left:0;top:78px;width:1200px;height:439px;background:#f3f3f3}
.hero-photo{position:absolute;left:500px;top:0;width:700px;height:439px;
  background:
    linear-gradient(180deg,rgba(255,255,255,.0) 60%,rgba(210,210,210,.5) 100%),
    linear-gradient(90deg,#f3f3f3 0%,#e2e2e2 18%,#bdbdbd 38%,#6e6e6e 58%,#3a3a3a 72%,#8c8c8c 86%,#d6d6d6 100%)}
.hero-copy{position:absolute;left:198px;top:146px;width:320px;font-size:16px;line-height:22px;color:#333}
.hero-copy .accent{color:var(--gold-text)}
.cta{position:absolute;left:198px;top:261px;width:163px;height:40px;background:#1d1d1d;color:#fff;font-size:12px;font-weight:600;display:flex;align-items:center;justify-content:center;border-radius:2px}
.slider-dots{position:absolute;left:198px;top:379px;display:flex;gap:9px}
.slider-dots i{width:9px;height:9px;border-radius:50%;background:#333}
.slider-dots i.on{background:var(--olive)}

/* services */
.services{position:absolute;left:0;top:517px;width:1200px;height:765px;
  background:linear-gradient(120deg,#f2f2f2 0%,#e4e4e4 30%,#f5f5f5 55%,#d9d9d9 80%,#ececec 100%)}
.section-title{position:absolute;left:0;width:1200px;text-align:center;font-size:22px;font-weight:600;color:#2b2b2b}
.service-card{position:absolute;width:388px;height:257px}
.service-card.photo-machine{background:linear-gradient(160deg,#f0f0f0 0%,#b9b9b9 35%,#6d6d6d 60%,#cfcfcf 100%)}
.service-card.photo-parts{background:linear-gradient(135deg,#5a5a5a 0%,#c9c9c9 30%,#7a7a7a 55%,#e5e5e5 80%,#9a9a9a 100%)}
.service-card.photo-actuator{background:linear-gradient(200deg,#d4d4d4 0%,#9c9c9c 40%,#3d3d3d 60%,#b5b5b5 100%)}
.service-card .label{position:absolute;left:11px;bottom:16px;width:142px;height:72px;background:var(--olive);color:#fff;font-weight:600;font-size:17px;display:flex;align-items:center;padding-left:16px}
.service-card.featured{background:linear-gradient(135deg,#6a6139,#544d2d);color:#fff;padding:38px 26px}
.service-card.featured h3{font-size:18px;font-weight:600;line-height:22px}
.service-card.featured p{font-size:9.5px;line-height:17px;margin-top:12px;color:#e8e3cf}
.read-more-btn{display:inline-block;margin-top:20px;background:#8a8468;color:#eee;font-size:9px;padding:9px 18px}

/* products */
.rule{position:absolute;left:200px;width:798px;border-top:1px dashed var(--line)}
.product-icon{position:absolute;background:#1a1a1a;border-radius:4px}
.product-name{position:absolute;width:200px;text-align:center;font-size:16px;font-weight:600;color:var(--gold-text)}
.product-underline{position:absolute;left:816px;top:1583px;width:109px;height:3px;background:#888}
.product-shot{position:absolute;top:1628px;width:184px;height:182px;background:linear-gradient(160deg,#f1f1f1 0%,#e6e6e6 55%,#dcdcdc 100%)}
.product-shot::after{content:"";position:absolute;left:30px;top:40px;width:124px;height:100px;border-radius:6px}
.product-shot.board::after{background:linear-gradient(135deg,#3f8a70,#2a6b58)}
.product-shot.box::after{left:40px;top:52px;width:104px;height:78px;background:linear-gradient(135deg,#2e2e2e,#151515)}
.product-shot.cable::after{left:90px;top:96px;width:64px;height:44px;background:linear-gradient(135deg,#4f8c74,#2f6b56)}
.product-caption{position:absolute;top:1846px;width:184px;text-align:center;font-size:15px;color:#333}

/* news */
.news{position:absolute;left:0;top:1925px;width:1200px;height:583px;background:var(--news-bg)}
.news .section-title{color:#2f2c1f}
.news .rule{top:136px;border-top-color:#ece6cc}
.news-arrow{position:absolute;top:80px}
.date-box{position:absolute;width:120px;height:113px;background:linear-gradient(#ffffff,#e2e2e2);box-shadow:0 3px 6px rgba(0,0,0,.3);text-align:center;font-weight:300;font-size:28px;line-height:28px;color:#333;padding-top:14px}
.date-box b{display:block;font-weight:700;font-size:22px;color:var(--gold-text)}
.news-text{position:absolute;width:250px;font-size:15px;line-height:23px;color:#fff}
.news-text .more{display:block;margin-top:16px;color:#3a3624}

/* footer */
.site-footer .brand{left:538px;top:2574px}
.footer-nav{position:absolute;left:0;top:2630px;width:1200px;text-align:center;font-size:12px;color:#333;text-transform:uppercase}
.footer-nav span{margin:0 18px}
.copyright{position:absolute;left:0;top:2667px;width:1200px;text-align:center;font-size:12px;color:#333}
</style>
</head>
<body>

<header class="site-header">
  <div class="brand"><span class="brand-mark"></span>VARNEL</div>
  <nav>
    <span class="nav-link active" style="left:435px">Home</span>
    <span class="nav-link" style="left:512px">Services</span>
    <span class="nav-link" style="left:603px">Products</span>
    <span class="nav-link" style="left:683px">Examples</span>
    <span class="nav-link" style="left:767px">Download</span>
    <span class="nav-link" style="left:849px">Contacts</span>
  </nav>
  <div class="lang-flag" role="img" aria-label="English language flag"></div>
  <div class="login-btn"><span class="dot"></span>LOGIN</div>
</header>

<section class="hero">
  <div class="hero-photo" role="img" aria-label="Two businessmen reviewing a tablet, black and white photo"></div>
  <p class="hero-copy"><span class="accent">VARNEL Ltd.</span> Designs systems in which electronics, software and mechanics are perfectly integrated to achieve uncompromising performance.</p>
  <div class="cta">GET STARTED</div>
  <div class="slider-dots"><i class="on"></i><i></i><i></i><i></i></div>
</section>

<section class="services">
  <h2 class="section-title" style="top:64px">OUR SERVICES</h2>
  <article class="service-card featured" style="left:200px;top:137px">
    <h3>Simulation<br>&amp; Modeling</h3>
    <p>Through a multi-physics modelling approach, Varnel Ltd. can integrate into the simulation all the main elements of the system, thus enabling a representation of all interactions between the mechanical, electrical and regulation modules.</p>
    <span class="read-more-btn">Read More</span>
  </article>
  <article class="service-card photo-machine" style="left:612px;top:137px" role="img" aria-label="CNC milling machine photo">
    <div class="label">Electronics</div>
  </article>
  <article class="service-card photo-parts" style="left:200px;top:423px" role="img" aria-label="Machined aluminium parts photo">
    <div class="label">Mechanics</div>
  </article>
  <article class="service-card photo-actuator" style="left:612px;top:423px" role="img" aria-label="Linear actuator with motor photo">
    <div class="label">Software</div>
  </article>
</section>

<section class="products">
  <h2 class="section-title" style="top:1346px">OUR PRODUCTS</h2>
  <div class="rule" style="top:1399px"></div>

  <div class="product-icon" style="left:290px;top:1462px;width:76px;height:56px" role="img" aria-label="Flying seabird silhouette"></div>
  <div class="product-icon" style="left:570px;top:1460px;width:70px;height:60px" role="img" aria-label="Perched bird silhouette"></div>
  <div class="product-icon" style="left:855px;top:1446px;width:40px;height:80px" role="img" aria-label="Penguin silhouette"></div>

  <div class="product-name" style="left:228px;top:1547px">HERON</div>
  <div class="product-name" style="left:505px;top:1547px">KESTREL</div>
  <div class="product-name" style="left:774px;top:1547px">PLOVER</div>
  <div class="product-underline"></div>

  <div class="product-shot board" style="left:200px" role="img" aria-label="Circuit board product photo"></div>
  <div class="product-shot box" style="left:406px" role="img" aria-label="Black module enclosure product photo"></div>
  <div class="product-shot board" style="left:612px" role="img" aria-label="Green circuit board product photo"></div>
  <div class="product-shot cable" style="left:818px" role="img" aria-label="Cabled module with board product photo"></div>

  <div class="product-caption" style="left:200px">Internal Card (top)</div>
  <div class="product-caption" style="left:406px">Internal Card (top)</div>
  <div class="product-caption" style="left:612px">Internal Card (top)</div>
  <div class="product-caption" style="left:818px">Internal Card (top)</div>
</section>

<section class="news">
  <h2 class="section-title" style="top:76px">IN THE NEWS</h2>
  <svg class="news-arrow" style="left:200px" width="16" height="24" viewBox="0 0 16 24"><path d="M12 3 L4 12 L12 21" fill="none" stroke="#fff" stroke-width="3"/></svg>
  <svg class="news-arrow" style="left:986px" width="16" height="24" viewBox="0 0 16 24"><path d="M4 3 L12 12 L4 21" fill="none" stroke="#fff" stroke-width="3"/></svg>
  <div class="rule"></div>

  <div class="date-box" style="left:200px;top:187px">8TH<br>SEP<b>2016</b></div>
  <div class="news-text" style="left:336px;top:180px">The Varnel team will be present at the stand A16 of Techmesse exhibition in Bern, between 6 and<span class="more">Read More +</span></div>

  <div class="date-box" style="left:610px;top:187px">9TH<br>SEP<b>2016</b></div>
  <div class="news-text" style="left:745px;top:180px">Added the 'application' page, showing some of the developments of Varnel Ltd.<span class="more">Read More +</span></div>

  <div class="date-box" style="left:200px;top:347px">8TH<br>SEP<b>2016</b></div>
  <div class="news-text" style="left:336px;top:340px">Sed ut perspiciatis unde omnis iste natus error sit voluptatem accusantium doloremque laudantium<span class="more">Read More +</span></div>

  <div class="date-box" style="left:610px;top:347px">9TH<br>SEP<b>2016</b></div>
  <div class="news-text" style="left:745px;top:340px">The Varnel team will be present at the stand A16 of Techmesse exhibition in Bern, between 6<span class="more">Read More +</span></div>
</section>

<footer class="site-footer">
  <div class="brand"><span class="brand-mark"></span>VARNEL</div>
  <nav class="footer-nav">Home<span>|</span>Services<span>|</span>Products<span>|</span>Examples<span>|</span>Download<span>|</span>Contacts</nav>
  <p class="copyright">© 2016 COMPANY NAME &nbsp;| ALL RIGHTS RESERVED</p>
</footer>

</body>
</html>
```